Website for legal expungement services with button to qualify/disqualify potential clients

Brightpath Record Renewal, LLC is a law firm focusing in legal expungement servcies (allowing people to erase criminal court records, police records, proseution files, etc). I want a more modern look which exudes confidence in the services. I am looking for a clean website that looks very polished. I want to keep the pages to a minimum, as I want the page not so much to answer questions, but to direct traffic to contact the law office. I would like the main focus point to be an button which would take a client through a series of questions to see if they would qualify for the services; this serves two purposes 1) to collect contact info for future marketing via email and 2) eliminate individuals who we are currently unable to help. A current theme that I have played around with are "Change so much, you'll need to reintroduce yourself" alongside a picture of a guys hand outstretched.
On the landing page, I would like a very brief and to the point explanation of what the service would be (i.e. "Leave your past in the past; expunge all your criminal records" ), followed by a list of benefits that it provides. (NB: included is a file "law post card-02" that includes the main benefits to expungement). Also included are two logo files for a more updated logo I currently use ("BRR Logo" and BRR Logo2") (NB: I'm open to revisions on this as well). Lastly, I've had two very minor 'ads' that I did ("postcard back" and "KVT Ad") that I like the idea of.

Target Market(s)

Middle/upper-middle class, mostly male, people with a criminal record or criminal accusation

Industry/Entity Type

Legal Services

Coding

Coded - Design and coding required

Requirements
Must have
• Button that attracts attention up front (possibly stand out coloring) to click to open up a series of questions to qualify/eliminate prospects, and simultaneously gather their info. Also, must be mobile friendly.

```html
<!DOCTYPE html>
<html lang="en">
<head>
<meta charset="utf-8">
<title>Brightpath Record Renewal</title>
<link href="https://fonts.googleapis.com/css2?family=Poppins:wght@400;500;600;700&display=swap" rel="stylesheet">
<style>
:root{
  --navy:#0c3c7c;
  --navy-deep:#0a3266;
  --ink:#222;
  --body:#3a3a3a;
  --line:#c9c9c9;
  --white:#fff;
  --black:#000;
}
*{margin:0;padding:0;box-sizing:border-box}
html,body{width:1200px;height:4471px;overflow:hidden;background:var(--white)}
body{font-family:"Poppins",sans-serif;color:var(--body);position:relative}
.abs{position:absolute}
section,header,footer,.topbar{position:absolute;left:0;width:1200px}
a{color:inherit;text-decoration:none}

/* top bar */
.topbar{top:0;height:52px;background:var(--navy);color:var(--white);font-size:15px}
.topbar .item{top:15px;display:flex;align-items:center;gap:8px}
.social-dot{width:13px;height:13px;border-radius:50%;background:var(--white);top:21px}

/* header */
.site-header{top:52px;height:101px;background:var(--white)}
.brand-box{left:111px;top:28px;width:122px;height:47px;border:2px solid var(--navy);color:var(--navy);font-size:26px;letter-spacing:10px;text-align:center;line-height:43px;padding-left:10px;font-weight:500}
.brand-rule{left:267px;top:5px;width:2px;height:89px;background:var(--navy)}
.brand-name{left:304px;top:27px;color:var(--navy);font-size:18px;line-height:25px;font-weight:500;letter-spacing:1.5px}
.nav a{position:absolute;top:38px;font-size:15px;color:var(--navy)}
.nav .active{left:664px;top:31px;width:55px;height:35px;border:1.5px solid var(--navy);text-align:center;line-height:32px}

/* hero */
.hero{top:153px;height:716px;background:radial-gradient(ellipse at 55% 60%,#6e5446 0%,#3f3a3c 35%,#2b3038 65%,#1c222b 100%)}
.hero-quote{left:195px;top:146px;width:813px;height:330px;border:7px solid var(--navy);display:flex;align-items:center;justify-content:center;text-align:center;color:var(--white);font-size:74px;font-weight:600;line-height:93px}
.hero-btn{left:476px;top:521px;width:240px;height:40px;background:var(--white);color:var(--navy);font-size:21px;text-align:center;line-height:40px}
.chev{top:340px}

/* benefit strip */
.benefits-strip{top:869px;height:126px;display:flex;border-top:1px solid var(--line);border-bottom:1px solid var(--line)}
.benefit{position:relative;width:240px;height:126px;border-right:1px solid var(--line);color:var(--body);font-size:15px;line-height:26px}
.benefit:first-child{border-left:1px solid var(--line)}
.benefit.is-active{background:var(--navy);color:var(--white)}
.benefit .icon{position:absolute;left:12px;top:14px}
.benefit .text{position:absolute;left:62px;top:8px;width:172px}
.benefit .go{position:absolute;left:64px;top:94px}
.dots{top:1010px;left:570px;display:flex;gap:11px}
.dots span{width:11px;height:11px;border-radius:50%;background:var(--navy)}

/* about */
.about-title{left:54px;top:1160px;font-size:38px;line-height:51px;font-weight:700;color:var(--navy)}
.about-text{left:64px;top:1282px;width:420px;font-size:15px;line-height:30.3px;color:var(--body)}
.btn-navy{background:var(--navy);color:var(--white);font-size:20px;text-align:center}
.about-frame{left:634px;top:1108px;width:419px;height:487px;border:3px solid var(--navy);border-right:none;border-bottom:none}
.about-photo{left:646px;top:1124px;width:441px;height:514px;background:linear-gradient(160deg,#c8ccca 0%,#8a7d74 45%,#6b4a3d 70%,#3d3b3c 100%)}

/* services */
.section-title{width:1200px;text-align:center;font-size:38px;font-weight:700;color:var(--navy)}
.svc-frame{width:450px;height:289px;border:3px solid var(--navy);border-bottom:none;border-right:none}
.svc-frame::after{content:"";position:absolute;right:0;top:-3px;width:3px;height:14px;background:var(--navy)}
.svc-photo{width:467px;height:311px}
.svc-card{width:405px;height:238px;background:var(--white);box-shadow:0 2px 10px rgba(0,0,0,.25);text-align:center;color:var(--ink)}
.svc-card .icon{position:absolute;left:0;width:405px;top:20px;display:flex;justify-content:center}
.svc-card h3{position:absolute;left:0;width:405px;top:98px;font-size:25px;line-height:30px;font-weight:600}
.svc-card .go{position:absolute;left:190px;top:185px}

/* public records */
.records{top:2380px;height:488px;background:var(--navy);color:var(--white)}
.split-photo{top:0;width:600px;height:488px}
.split-title{font-size:40px;line-height:51px;font-weight:600}
.bullets li{list-style:none;position:absolute;font-size:15px;padding-left:28px}
.bullets li::before{content:"";position:absolute;left:0;top:7px;width:9px;height:9px;border-radius:50%;background:var(--white)}
.btn-white{background:var(--white);color:var(--navy);font-size:20px;text-align:center}

/* contact */
.contact-title{top:2935px;width:1200px;text-align:center;font-size:40px;line-height:51px;font-weight:600;color:var(--navy)}
.contact-phone{top:3110px;width:1200px;text-align:center;font-size:38px;color:var(--ink)}

/* cases */
.cases{top:3321px;height:488px;background:var(--navy);color:var(--white)}

/* partners */
.partners{top:3809px;height:244px;background:var(--white)}
.partner-card{left:63px;top:0;width:1026px;height:244px;background:var(--white);box-shadow:0 3px 8px rgba(0,0,0,.18)}
.partner{display:flex;align-items:center;gap:14px;color:var(--navy);font-size:26px;font-weight:600}
.partner .mark{width:30px;height:30px;background:var(--navy)}

/* footer */
.site-footer{top:4053px;height:418px;background:var(--black);color:var(--white)}
.foot-box{left:307px;top:100px;width:191px;height:73px;border:3px solid var(--white);font-size:44px;letter-spacing:22px;text-align:center;line-height:67px;padding-left:22px}
.foot-rule{left:552px;top:60px;width:2px;height:146px;background:var(--white)}
.foot-name{left:613px;top:98px;font-size:30px;line-height:39px;letter-spacing:2px;font-weight:500}
.foot-social{top:256px;left:521px;display:flex;gap:34px}
.foot-social span{width:14px;height:14px;border-radius:50%;background:var(--white)}
.foot-links{top:310px;width:1200px;display:flex;justify-content:center;gap:20px;font-size:15px}
.foot-rule-h{top:367px;left:0;width:1200px;height:1px;background:#555}
.copyright{top:386px;width:1200px;text-align:center;font-size:11px}
</style>
</head>
<body>

<div class="topbar">
  <div class="abs item" style="left:111px">
    <svg width="16" height="12" viewBox="0 0 16 12"><rect x="0.5" y="0.5" width="15" height="11" fill="none" stroke="#fff"/><path d="M1 1l7 6 7-6" fill="none" stroke="#fff"/></svg>
    info@brightpathrenewal.com
  </div>
  <div class="abs item" style="left:440px">
    <svg width="16" height="16" viewBox="0 0 24 24"><path d="M6.6 10.8a15 15 0 006.6 6.6l2.2-2.2c.3-.3.7-.4 1-.2 1.1.4 2.3.6 3.6.6.6 0 1 .4 1 1V20c0 .6-.4 1-1 1A17 17 0 013 4c0-.6.4-1 1-1h3.5c.6 0 1 .4 1 1 0 1.3.2 2.5.6 3.6.1.3 0 .7-.2 1z" fill="#fff"/></svg>
    555-014-2290
  </div>
  <span class="abs social-dot" style="left:932px"></span>
  <span class="abs social-dot" style="left:977px"></span>
  <span class="abs social-dot" style="left:1026px"></span>
  <span class="abs social-dot" style="left:1073px"></span>
</div>

<header class="site-header">
  <div class="abs brand-box">BRR</div>
  <div class="abs brand-rule"></div>
  <div class="abs brand-name">BRIGHTPATH RECORD<br>RENEWAL</div>
  <nav class="nav">
    <a class="active">Home</a>
    <a style="left:737px">About Us</a>
    <a style="left:825px">Service</a>
    <a style="left:902px">Pages</a>
    <a style="left:969px">Blog</a>
    <a style="left:1023px">Contact</a>
  </nav>
</header>

<section class="hero" role="img" aria-label="Photo of an outstretched hand offered in greeting">
  <div class="abs hero-quote">"Change so much,<br>you'll need to<br>reintroduce yourself"</div>
  <a class="abs hero-btn">Book an Appointment</a>
  <svg class="abs chev" style="left:66px" width="20" height="32" viewBox="0 0 20 32"><path d="M16 3L4 16l12 13" fill="none" stroke="#fff" stroke-width="3"/></svg>
  <svg class="abs chev" style="left:1110px" width="20" height="32" viewBox="0 0 20 32"><path d="M4 3l12 13L4 29" fill="none" stroke="#fff" stroke-width="3"/></svg>
</section>

<section class="benefits-strip">
  <div class="benefit">
    <svg class="icon" width="44" height="44" viewBox="0 0 44 44"><circle cx="26" cy="12" r="10" fill="var(--navy)"/><text x="26" y="17" font-size="14" fill="#fff" text-anchor="middle" font-family="Poppins,sans-serif" font-weight="700">$</text><path d="M2 30h10l8 4h10c2 0 2 3 0 3H18M12 40h18l12-10c1-2-1-4-3-3l-9 5" fill="none" stroke="var(--navy)" stroke-width="3"/></svg>
    <div class="text">More and better job opportunities leading to higher income</div>
    <svg class="go" width="26" height="20" viewBox="0 0 26 20"><path d="M1 10h22M15 2l8 8-8 8" fill="none" stroke="var(--navy)" stroke-width="3"/></svg>
  </div>
  <div class="benefit">
    <svg class="icon" width="44" height="44" viewBox="0 0 44 44"><path d="M4 10l18-7 18 7-18 7z" fill="var(--navy)"/><path d="M34 12v8" stroke="var(--navy)" stroke-width="2"/><rect x="6" y="22" width="32" height="6" fill="var(--navy)"/><rect x="4" y="30" width="36" height="6" fill="none" stroke="var(--navy)" stroke-width="2.5"/></svg>
    <div class="text" style="top:16px">Better education opportunities</div>
    <svg class="go" width="26" height="20" viewBox="0 0 26 20"><path d="M1 10h22M15 2l8 8-8 8" fill="none" stroke="var(--navy)" stroke-width="3"/></svg>
  </div>
  <div class="benefit is-active">
    <svg class="icon" width="44" height="44" viewBox="0 0 44 44"><path d="M22 4l15 6v10c0 10-7 17-15 20-8-3-15-10-15-20V10z" fill="#fff"/><rect x="17" y="20" width="10" height="8" fill="var(--navy)"/><path d="M19 20v-3a3 3 0 016 0v3" fill="none" stroke="var(--navy)" stroke-width="2"/></svg>
    <div class="text" style="top:16px">Protecting your privacy</div>
    <svg class="go" width="26" height="20" viewBox="0 0 26 20"><path d="M1 10h22M15 2l8 8-8 8" fill="none" stroke="#fff" stroke-width="3"/></svg>
  </div>
  <div class="benefit">
    <svg class="icon" width="44" height="44" viewBox="0 0 44 44"><rect x="6" y="4" width="22" height="30" fill="var(--navy)"/><path d="M11 12h12M11 18h12M11 24h8" stroke="#fff" stroke-width="2.5"/><circle cx="31" cy="31" r="9" fill="var(--navy)" stroke="#fff" stroke-width="2"/><path d="M27 31l3 3 5-6" fill="none" stroke="#fff" stroke-width="2.5"/></svg>
    <div class="text" style="top:16px">Lower insurance premiums</div>
    <svg class="go" width="26" height="20" viewBox="0 0 26 20"><path d="M1 10h22M15 2l8 8-8 8" fill="none" stroke="var(--navy)" stroke-width="3"/></svg>
  </div>
  <div class="benefit">
    <svg class="icon" width="44" height="44" viewBox="0 0 44 44"><rect x="6" y="4" width="26" height="34" rx="2" fill="var(--navy)"/><rect x="11" y="10" width="6" height="6" fill="#fff"/><path d="M20 13h8M11 22h17M11 28h17" stroke="#fff" stroke-width="2.5"/></svg>
    <div class="text">Removing the stigma of having a criminal record</div>
    <svg class="go" width="26" height="20" viewBox="0 0 26 20"><path d="M1 10h22M15 2l8 8-8 8" fill="none" stroke="var(--navy)" stroke-width="3"/></svg>
  </div>
</section>
<div class="abs dots"><span></span><span></span><span></span></div>

<h2 class="abs about-title">The Benefits of<br>Expungement</h2>
<p class="abs about-text">Brightpath Record Renewal is 5-star rated firm, which has been formed with the passing of the State Expungement law of 2020. It is a subdivision of How your records Els awa the Alder Stone Law Group, and since its creation has helped over 100 New Mexican citizens &nbsp;successfully expunge their criminal records.</p>
<a class="abs btn-navy" style="left:66px;top:1541px;width:125px;height:42px;line-height:42px">Read More</a>
<div class="abs about-frame"></div>
<div class="abs about-photo" role="img" aria-label="Photo of a lawyer consulting with a client on a leather sofa"></div>

<h2 class="abs section-title" style="top:1714px">Our Services</h2>

<div class="abs svc-frame" style="left:64px;top:1796px"></div>
<div class="abs svc-photo" style="left:78px;top:1808px;background:linear-gradient(135deg,#2a221f 0%,#5b4a42 45%,#cfc9c4 80%,#e8e6e3 100%)" role="img" aria-label="Photo of hands signing a document with a pen"></div>
<div class="abs svc-card" style="left:109px;top:2055px">
  <div class="icon"><svg width="90" height="56" viewBox="0 0 90 56"><path d="M2 10l18-6 10 26-16 8z" fill="var(--navy)"/><path d="M88 10l-18-6-10 26 16 8z" fill="var(--navy)"/><path d="M30 14l14-4 10 4 14 2-6 20-10 10c-3 3-7 2-9-1l-9-9z" fill="var(--navy)" stroke="#fff" stroke-width="2"/><path d="M44 12l-10 10c-2 3 2 6 5 4l9-7" fill="none" stroke="#fff" stroke-width="2.5"/></svg></div>
  <h3>Leave your<br>past in the past</h3>
  <svg class="go" width="26" height="22" viewBox="0 0 26 22"><path d="M1 11h22M15 3l8 8-8 8" fill="none" stroke="var(--navy)" stroke-width="3"/></svg>
</div>

<div class="abs svc-frame" style="left:604px;top:1796px"></div>
<div class="abs svc-photo" style="left:618px;top:1808px;background:linear-gradient(120deg,#e9e2d8 0%,#d6c4ad 45%,#a88f73 75%,#4a4442 100%)" role="img" aria-label="Photo of a person reviewing paper records beside a laptop"></div>
<div class="abs svc-card" style="left:649px;top:2055px">
  <div class="icon"><svg width="66" height="70" viewBox="0 0 66 70"><rect x="6" y="2" width="46" height="62" rx="5" fill="var(--navy)"/><rect x="13" y="12" width="9" height="9" fill="none" stroke="#fff" stroke-width="2.5"/><path d="M27 16h16M13 30h30M13 38h30M13 46h20" stroke="#fff" stroke-width="3"/><circle cx="48" cy="54" r="12" fill="var(--navy)" stroke="#fff" stroke-width="2.5"/></svg></div>
  <h3>Expunge all<br>your criminal record</h3>
  <svg class="go" width="26" height="22" viewBox="0 0 26 22"><path d="M1 11h22M15 3l8 8-8 8" fill="none" stroke="var(--navy)" stroke-width="3"/></svg>
</div>

<section class="records">
  <h2 class="abs split-title" style="left:64px;top:40px">How your records are<br>seen by the public:</h2>
  <ul class="bullets">
    <li style="left:66px;top:155px">Public reporting (www.statecourts-records.org)</li>
    <li style="left:66px;top:202px">Police reports</li>
    <li style="left:66px;top:249px">State Department of Public Safety</li>
    <li style="left:66px;top:295px">District attorney prosecution files</li>
    <li style="left:66px;top:342px">Court records</li>
  </ul>
  <a class="abs btn-white" style="left:64px;top:396px;width:127px;height:40px;line-height:40px">Read More</a>
  <div class="abs split-photo" style="left:600px;background:linear-gradient(135deg,#6b3a20 0%,#9a5a34 40%,#d9cfc7 60%,#8a4a28 100%)" role="img" aria-label="Photo of hands holding a torn note reading criminal record"></div>
</section>

<h2 class="abs contact-title">To see if you qualify for<br>expungement or for additional<br>information,contact us</h2>
<div class="abs contact-phone">555-014-2290</div>
<a class="abs btn-navy" style="left:445px;top:3193px;width:146px;height:42px;line-height:42px">Get a Quote</a>
<a class="abs btn-navy" style="left:610px;top:3193px;width:146px;height:42px;line-height:42px">Learn More</a>

<section class="cases">
  <div class="abs split-photo" style="left:0;background:linear-gradient(120deg,#1f3d6b 0%,#3a5a86 40%,#d8dee6 60%,#2c4a78 100%)" role="img" aria-label="Photo of hands exchanging a signed document"></div>
  <h2 class="abs split-title" style="left:672px;top:72px">What types of cases<br>qualify:</h2>
  <ul class="bullets">
    <li style="left:677px;top:206px">Criminal accusations that were dismissed</li>
    <li style="left:677px;top:253px">Criminal cases that went into a</li>
    <li style="left:677px;top:300px">diversionary program</li>
  </ul>
  <a class="abs btn-white" style="left:679px;top:365px;width:129px;height:40px;line-height:40px">Read More</a>
</section>

<section class="partners">
  <div class="abs partner-card">
    <div class="abs partner" style="left:140px;top:100px"><span class="mark"></span>Brightpath Record Renewal</div>
    <div class="abs partner" style="left:600px;top:100px"><span class="mark"></span>Alder Stone Law Group</div>
  </div>
</section>

<footer class="site-footer">
  <div class="abs foot-box">BRR</div>
  <div class="abs foot-rule"></div>
  <div class="abs foot-name">BRIGHTPATH RECORD<br>RENEWAL</div>
  <div class="abs foot-social"><span></span><span></span><span></span><span></span></div>
  <nav class="abs foot-links"><a>Home</a><a>About Us</a><a>Service</a><a>Pages</a><a>Blog</a><a>Contact</a></nav>
  <div class="abs foot-rule-h"></div>
  <div class="abs copyright">© Copyright | Brightpath Record Renewal | All right reserved.</div>
</footer>

</body>
</html>
```